4 page brochure for Logistics Company

Need a 4 page brochure (ie folded A3) for a Logistics company.
Service is a virtual network of warehouse and logistics companies.
Style is professional but accessible.
We have logo and styles designed and will upload these.
We have identified example images that could be used in the brochure.
Content will be uploaded also.
Reason: A couple of designers requested more time
Am giving another 24 hours to finalise and will then select most suitable design
Target Market(s)
40 to 60 year old business owners (traditional) - Australian
Industry/Entity Type
It Company
Requirements
Must have
- Professional
Should not have
- Nothing tacky

```html
<!DOCTYPE html>
<html lang="en">
<head>
<meta charset="utf-8">
<title>Southern Freight Alliance – Brochure Spread</title>
<link href="https://fonts.googleapis.com/css2?family=Open+Sans:wght@300;400;600;700&display=swap" rel="stylesheet">
<style>
  :root {
    --bg: #e4e6e8;
    --paper: #ffffff;
    --accent-blue: #3b8fcf;
    --heading-blue: #3a86c8;
    --slate: #6f8594;
    --slate-dark: #5d7382;
    --text: #555d63;
    --white: #ffffff;
    --map-tone: #ece9de;
    --warehouse-light: #f1eee8;
    --warehouse-mid: #d6c2a0;
    --warehouse-dark: #9a8466;
  }
  * { box-sizing: border-box; margin: 0; padding: 0; }
  html, body { width: 1200px; height: 863px; overflow: hidden; }
  body {
    background: var(--bg);
    font-family: "Open Sans", sans-serif;
    color: var(--text);
    position: relative;
  }
  .spread {
    position: absolute;
    left: 48px; top: 41px;
    width: 1104px; height: 780px;
    display: flex;
    box-shadow: 0 10px 30px rgba(0,0,0,0.18);
  }
  .page {
    position: relative;
    width: 552px; height: 780px;
    background: var(--paper);
    overflow: hidden;
  }
  .page--team { border-right: 1px solid #e3e5e7; }
  .corner-swoosh { position: absolute; top: 0; width: 200px; height: 70px; }
  .page--team .corner-swoosh { left: 0; }
  .page--routes .corner-swoosh { right: 0; }

  .team-title {
    position: absolute; left: 190px; top: 38px;
    font-weight: 300; font-size: 27px; color: var(--heading-blue);
  }
  .team-intro {
    position: absolute; left: 210px; top: 78px; width: 310px;
    font-size: 8.5px; line-height: 1.35; color: var(--text);
  }
  .brand-name {
    position: absolute; left: 30px; top: 116px;
    font-size: 13px; font-weight: 400; letter-spacing: 0.3px;
    color: var(--heading-blue); text-transform: uppercase;
  }

  .team-row {
    position: absolute; left: 30px; width: 500px;
    display: flex; color: var(--white);
  }
  .team-row--1 { top: 140px; height: 168px; }
  .team-row--2 { top: 322px; height: 152px; }
  .team-row--3 { top: 488px; height: 232px; }
  .expertise {
    background: linear-gradient(90deg, var(--slate-dark), var(--slate));
    padding: 14px 14px 12px 18px; width: 212px; flex-shrink: 0;
  }
  .expertise h3 { font-size: 10.5px; font-weight: 700; line-height: 1.3; margin-bottom: 3px; }
  .expertise p { font-size: 8.5px; line-height: 1.3; margin-bottom: 5px; }
  .expertise p + h3 { margin-top: 4px; }
  .expertise ul { list-style: none; margin-top: 6px; }
  .expertise li { font-size: 9.5px; line-height: 1.3; margin-bottom: 11px; }
  .profile {
    background: var(--accent-blue);
    width: 125px; flex-shrink: 0;
    display: flex; flex-direction: column; align-items: center; justify-content: center;
    text-align: center; padding: 6px;
  }
  .portrait {
    width: 84px; height: 84px; border-radius: 50%;
    border: 4px solid var(--white);
    background: radial-gradient(circle at 50% 40%, #c9d3dc, #7f93a4);
    margin-bottom: 8px;
  }
  .profile-name { font-size: 12px; font-weight: 400; }
  .profile-credentials { font-size: 7.5px; line-height: 1.3; margin-top: 2px; }
  .highlights {
    flex: 1; background: var(--slate);
    list-style: none; padding: 14px 10px 10px 10px;
  }
  .highlights li {
    display: flex; gap: 5px; font-size: 8px; line-height: 1.3; margin-bottom: 8px;
  }
  .tick { width: 10px; height: 10px; flex-shrink: 0; margin-top: 1px; }

  .routes-title {
    position: absolute; left: 60px; top: 70px;
    font-size: 15px; font-weight: 400; color: var(--heading-blue);
    letter-spacing: 0.3px; text-transform: uppercase;
  }
  .route-map {
    position: absolute; left: 60px; top: 98px; width: 440px; height: 300px;
    background: radial-gradient(ellipse at 50% 50%, var(--map-tone) 55%, #f6f5f1 75%, var(--paper) 90%);
  }
  .map-date {
    position: absolute; left: 62px; top: 410px; font-size: 7.5px; color: #9aa2a8;
  }
  .warehouse-photo {
    position: absolute; left: 0; bottom: 0; width: 552px; height: 360px;
    background:
      linear-gradient(180deg, var(--paper) 0%, rgba(255,255,255,0) 28%),
      linear-gradient(90deg, var(--warehouse-light) 0%, var(--warehouse-mid) 45%, #eceae6 60%, var(--warehouse-mid) 75%, var(--warehouse-dark) 100%);
  }
  .web-address {
    position: absolute; right: 36px; bottom: 46px;
    font-size: 12px; color: #5b5148; letter-spacing: 0.4px;
  }
</style>
</head>
<body>
  <main class="spread">
    <section class="page page--team">
      <svg class="corner-swoosh" viewBox="0 0 200 70" aria-hidden="true">
        <defs>
          <linearGradient id="swooshLeft" x1="0" y1="0" x2="1" y2="1">
            <stop offset="0" stop-color="#123f7a"/>
            <stop offset="1" stop-color="#2f7fcf"/>
          </linearGradient>
        </defs>
        <path d="M0 0 H200 C150 8 110 30 70 70 H0 Z" fill="url(#swooshLeft)"/>
        <path d="M160 4 C120 16 95 40 78 70" fill="none" stroke="#8a98a4" stroke-width="2"/>
      </svg>

      <h1 class="team-title">Our team (Who?)</h1>
      <p class="team-intro">With over 30 years of experience in warehouse, logistics and transportation and over 30 years of history in mergers, acquisitions and business sales, the SFA team is uniquely qualified to deliver outcomes to its members.</p>
      <h2 class="brand-name">Southern Freight Alliance</h2>

      <article class="team-row team-row--1">
        <div class="expertise">
          <h3>Logistics industry expertise:</h3>
          <p>Directors have &gt;30 years' experience in warehouse, logistics and transportation</p>
          <h3>Credibility from track record:</h3>
          <p>30 year history in M&amp;A and business sales</p>
          <p>National footprint</p>
          <p>Operates under an AFSL</p>
        </div>
        <div class="profile">
          <div class="portrait" role="img" aria-label="Portrait photograph of Graham Whitfield"></div>
          <div class="profile-name">Graham Whitfield</div>
          <div class="profile-credentials">Bcomm, FAICD, CPA, FCILT</div>
        </div>
        <ul class="highlights">
          <li><svg class="tick" viewBox="0 0 10 10"><circle cx="5" cy="5" r="4.3" fill="none" stroke="#fff" stroke-width="1"/><path d="M3 5.2 L4.5 6.6 L7.2 3.6" fill="none" stroke="#fff" stroke-width="1.1"/></svg>30 years' warehouse, logistics, transportation experience in expansion, mergers, acquisitions and divestment</li>
          <li><svg class="tick" viewBox="0 0 10 10"><circle cx="5" cy="5" r="4.3" fill="none" stroke="#fff" stroke-width="1"/><path d="M3 5.2 L4.5 6.6 L7.2 3.6" fill="none" stroke="#fff" stroke-width="1.1"/></svg>Established a national warehousing company</li>
          <li><svg class="tick" viewBox="0 0 10 10"><circle cx="5" cy="5" r="4.3" fill="none" stroke="#fff" stroke-width="1"/><path d="M3 5.2 L4.5 6.6 L7.2 3.6" fill="none" stroke="#fff" stroke-width="1.1"/></svg>Managed sale and acquisition of warehouse business</li>
        </ul>
      </article>

      <article class="team-row team-row--2">
        <div class="expertise">
          <h3>M&amp;A and advisory expertise:</h3>
          <p>&gt; $10B in combined transaction experience</p>
          <p>Tier-1 level M&amp;A and advisory experience</p>
          <p>Highly disciplined approach to business sales</p>
        </div>
        <div class="profile">
          <div class="portrait" role="img" aria-label="Portrait photograph of Adrian Korvel"></div>
          <div class="profile-name">Adrian Korvel</div>
          <div class="profile-credentials">B Eng, MAppFin, GAICD, FFinsia, CPEng, RPEQ</div>
        </div>
        <ul class="highlights">
          <li><svg class="tick" viewBox="0 0 10 10"><circle cx="5" cy="5" r="4.3" fill="none" stroke="#fff" stroke-width="1"/><path d="M3 5.2 L4.5 6.6 L7.2 3.6" fill="none" stroke="#fff" stroke-width="1.1"/></svg>&gt;25 years' international consulting, advisory experience</li>
          <li><svg class="tick" viewBox="0 0 10 10"><circle cx="5" cy="5" r="4.3" fill="none" stroke="#fff" stroke-width="1"/><path d="M3 5.2 L4.5 6.6 L7.2 3.6" fill="none" stroke="#fff" stroke-width="1.1"/></svg>Mergers, acquisitions and divestment experience</li>
          <li><svg class="tick" viewBox="0 0 10 10"><circle cx="5" cy="5" r="4.3" fill="none" stroke="#fff" stroke-width="1"/><path d="M3 5.2 L4.5 6.6 L7.2 3.6" fill="none" stroke="#fff" stroke-width="1.1"/></svg>Large bid management credentials leading bids &gt; $500M</li>
          <li><svg class="tick" viewBox="0 0 10 10"><circle cx="5" cy="5" r="4.3" fill="none" stroke="#fff" stroke-width="1"/><path d="M3 5.2 L4.5 6.6 L7.2 3.6" fill="none" stroke="#fff" stroke-width="1.1"/></svg>Responsible manager for Australian Financial Services License</li>
        </ul>
      </article>

      <article class="team-row team-row--3">
        <div class="expertise">
          <h3>Breadth of expertise:</h3>
          <ul>
            <li>Preparation and optimisation for sale</li>
            <li>Business sales</li>
            <li>Business acquisition and roll-ups</li>
            <li>Logistics tender management</li>
            <li>Logistics contract management</li>
            <li>Professional business development</li>
            <li>Business/profit improvement</li>
          </ul>
        </div>
        <div class="profile">
          <div class="portrait" role="img" aria-label="Portrait photograph of Neil Harcourt"></div>
          <div class="profile-name">Neil Harcourt</div>
          <div class="profile-credentials">CA, FCA, CEP</div>
        </div>
        <ul class="highlights">
          <li><svg class="tick" viewBox="0 0 10 10"><circle cx="5" cy="5" r="4.3" fill="none" stroke="#fff" stroke-width="1"/><path d="M3 5.2 L4.5 6.6 L7.2 3.6" fill="none" stroke="#fff" stroke-width="1.1"/></svg>Ex-CFO of ultra-high growth businesses</li>
          <li><svg class="tick" viewBox="0 0 10 10"><circle cx="5" cy="5" r="4.3" fill="none" stroke="#fff" stroke-width="1"/><path d="M3 5.2 L4.5 6.6 L7.2 3.6" fill="none" stroke="#fff" stroke-width="1.1"/></svg>Highly experienced in business roll-up strategies</li>
          <li><svg class="tick" viewBox="0 0 10 10"><circle cx="5" cy="5" r="4.3" fill="none" stroke="#fff" stroke-width="1"/><path d="M3 5.2 L4.5 6.6 L7.2 3.6" fill="none" stroke="#fff" stroke-width="1.1"/></svg>Completed over 25 acquisitions and implementations</li>
          <li><svg class="tick" viewBox="0 0 10 10"><circle cx="5" cy="5" r="4.3" fill="none" stroke="#fff" stroke-width="1"/><path d="M3 5.2 L4.5 6.6 L7.2 3.6" fill="none" stroke="#fff" stroke-width="1.1"/></svg>Executed divestment and merger programmes</li>
        </ul>
      </article>
    </section>

    <section class="page page--routes">
      <svg class="corner-swoosh" viewBox="0 0 200 70" aria-hidden="true">
        <defs>
          <linearGradient id="swooshRight" x1="1" y1="0" x2="0" y2="1">
            <stop offset="0" stop-color="#123f7a"/>
            <stop offset="1" stop-color="#2f7fcf"/>
          </linearGradient>
        </defs>
        <path d="M200 0 H0 C50 8 90 30 130 70 H200 Z" fill="url(#swooshRight)"/>
        <path d="M40 4 C80 16 105 40 122 70" fill="none" stroke="#8a98a4" stroke-width="2"/>
      </svg>

      <h2 class="routes-title">Australia Transportation Route</h2>
      <div class="route-map" role="img" aria-label="Map of Australia showing the network's colour-coded transport routes between capital cities and regional centres"></div>
      <p class="map-date">April 2013</p>

      <div class="warehouse-photo" role="img" aria-label="Photograph of a large warehouse aisle with tall racking stacked with cartons and pallets"></div>
      <p class="web-address">www.southfreightalliance.com.au</p>
    </section>
  </main>
</body>
</html>
```